Research and Innovation programme/projects in WOOD based industries

1.Pramenova s.r.o. (offical registered brand name of our company)
-Managing technology development projects
-International cooperation and development European projects
Our company was founded in 2008 and started to work as a counsilary company operating in the section of european funds administrated by Czech republic. Nowadays we are specializing on projects in the sphere of science and research co-financed by EU.Since 6.6.2013 we are registered under European comission for a purpose of broad support of transnational projects.

Target Market(s)

We are primarily focused on european companies, which stand behind the latest research and innovation of sawing, planing, glulam and logging technologies based on wooden materials.

Coding

Coded - Design and coding required

Number of Pages Required

5+ page

Font styles to use
Serif

Colors
cadf82
abd037
9bcb3c
fee18a
ffcf3e
ffc214

Requirements
Must have
• The web will exist in three possible languages in czech, english and deutsch.
• First page : introduction of a company
• Second page : Area of expertise
• Third page: servicies our company provides
• Fourth page: Our partners
• Fifth page: Conditions of our servicies
• Sixth page: Succesful projects
• - we would also love if we had possibility to add videos about our successful projects
• Seventh: Our team
• We are serious company in the sphere of funds and counsilary servicies, that is why we would love to have web design as representative as possible
• Take on mind that that we are specializing on development management, try to apply that on your design
• In the section of contacts, we would love to have photos of our team,
• This is our current site: http://www.pramenova-example.eu/cz/partneri.html
• This is how our concurency sites are lookin. Take these designs as an slight inspiration.
• http://www.lumatrava-example.sk/en/
• https://www2.brenvick-example.com/global/en.html
Nice to have
• Visible logo on the front page for the visitor.
• As a inspiration we provided link for our current web design, but we dont want to copy the current style, just look at the logo and the pages that exists on current web.
• !!!!!!We also uploaded file, where we explain how our cooperation with partner works. Especially in the part 2. section of service. Take that as an ispiration too, or use that to understand, what our company do.
Should not have
• We are serious company in the sphere of funds and counsilary servicies, that is why we would love to have web design representative as possible

```html
<!DOCTYPE html>
<html lang="en">
<head>
<meta charset="utf-8">
<title>1. Pramenova SRO – Beratungsfirma</title>
<link href="https://fonts.googleapis.com/css2?family=Quicksand:wght@500;600;700&family=Raleway:wght@400;500;600&display=swap" rel="stylesheet">
<style>
:root{
  --green:#8cc63f;
  --green-deep:#1f8a3c;
  --green-text:#6fb52c;
  --orange:#f4a81d;
  --yellow:#f2c21a;
  --ink:#333333;
  --muted:#6a6a6a;
  --dark:#1c1714;
  --light:#f4f4f4;
  --white:#ffffff;
}
*{margin:0;padding:0;box-sizing:border-box}
html,body{width:1200px;height:4930px;overflow:hidden}
body{font-family:"Raleway",sans-serif;color:var(--ink);background:var(--white);position:relative}
.abs{position:absolute}
h1,h2,h3,.btn,.brand-name,.nav a{font-family:"Quicksand",sans-serif}
.center{text-align:center}
.btn{position:absolute;display:flex;align-items:center;justify-content:center;border-radius:30px;color:var(--white);font-weight:600;text-decoration:none;background:linear-gradient(90deg,var(--green),var(--yellow))}
.btn-outline{background:none;border:2px solid var(--white)}
.section-title{position:absolute;left:0;width:1200px;text-align:center;font-size:31px;font-weight:700;color:var(--green-text);letter-spacing:.5px}
.section-title .accent{color:var(--orange)}
.section-sub{position:absolute;left:0;width:1200px;text-align:center;font-size:13px}
.photo{position:absolute}

/* header */
.header{top:0;left:0;width:1200px;height:102px}
.brand{position:absolute;display:flex;align-items:center;gap:18px}
.brand-mark{width:46px;height:32px;background:var(--green)}
.brand-name{font-size:21px;font-weight:700;color:var(--green-deep);line-height:1.1}
.brand-tag{font-size:14px;color:var(--orange);font-family:"Raleway",sans-serif;margin-top:3px}
.lang{position:absolute;left:951px;top:33px;width:138px;height:40px;border:1px solid #d8d8d8;border-radius:3px;background:#f7f7f7;font-size:12px;display:flex;align-items:center;padding-left:14px}
.lang::after{content:"";position:absolute;right:12px;top:17px;border:4px solid transparent;border-top-color:#444}
.nav{top:102px;left:0;width:1200px;height:59px;background:var(--green);display:flex;padding-left:111px}
.nav a{color:var(--white);text-decoration:none;font-size:13.5px;font-weight:600;display:flex;align-items:center;padding:0 18px;letter-spacing:.2px}
.nav a.active{background:var(--green-deep);padding:0 38px}

/* hero */
.hero{top:161px;left:0;width:1200px;height:685px;background:radial-gradient(ellipse at 55% 30%,#6b5038 0%,#3d2c20 45%,#211812 100%)}
.hero h1{position:absolute;top:312px;width:1200px;text-align:center;font-size:66px;color:var(--yellow);font-weight:700;letter-spacing:1px}
.hero p{position:absolute;top:406px;left:250px;width:700px;text-align:center;color:var(--white);font-size:19px;line-height:30px}
.arrow{position:absolute;top:322px;width:36px;height:36px;border:2px solid var(--white);border-radius:50%}

/* welcome */
.welcome-text{position:absolute;top:976px;left:258px;width:684px;text-align:center;font-size:12.5px;line-height:27.5px;color:var(--ink)}

/* expertise */
.expertise-band{top:1307px;left:0;width:1200px;height:444px;background:linear-gradient(100deg,var(--green) 0%,var(--green) 35%,#b8c524 70%,var(--yellow) 100%)}
.expertise h2{position:absolute;left:704px;top:1362px;font-size:31px;color:var(--white);font-weight:600}
.expertise p{position:absolute;left:704px;top:1420px;width:385px;text-align:justify;font-size:12px;line-height:27.5px;color:var(--white)}

/* services */
.service{position:absolute;top:1928px;width:280px;text-align:center}
.service svg{display:block;margin:0 auto}
.service h3{margin-top:28px;font-family:"Raleway",sans-serif;font-size:16px;font-weight:500;letter-spacing:.4px;color:#333}
.service p{margin-top:14px;font-size:12px;line-height:26px;color:var(--muted)}

/* partners */
.partners{top:2197px;left:0;width:1200px;height:389px;background:linear-gradient(180deg,#231a14,#171210)}
.partner{position:absolute;top:2343px;width:180px;height:180px;border-radius:50%;background:var(--white)}

/* conditions */
.conditions-box{top:2775px;left:534px;width:530px;height:379px;border:3px solid var(--green);background:var(--white)}
.conditions-box h2{position:absolute;left:29px;top:47px;font-size:28px;font-weight:700;color:var(--green-text)}
.conditions-box h2 .accent{color:var(--orange)}
.conditions-box p{position:absolute;left:31px;top:102px;width:466px;text-align:justify;font-size:12.5px;line-height:28.3px}

/* projects */
.projects-band{top:3219px;left:0;width:1200px;height:276px;background:var(--green)}
.play{position:absolute;left:555px;top:3592px;width:92px;height:92px;border-radius:50%;background:rgba(140,30,70,.85);border:3px solid var(--white)}

/* team */
.team-band{top:3981px;left:0;width:1200px;height:490px;background:var(--light)}
.team-title{position:absolute;left:111px;top:4068px;font-size:31px;font-weight:700;color:var(--orange)}
.team-text{position:absolute;left:111px;top:4126px;width:380px;text-align:justify;font-size:12px;line-height:24.5px}
.member{position:absolute;top:4039px;width:260px;height:381px}
.member .portrait{width:260px;height:300px;background:linear-gradient(180deg,#7a6a58,#3b3129)}
.member .name{height:81px;background:var(--green);color:var(--white);font-family:"Quicksand",sans-serif;font-weight:700;font-size:20px;display:flex;align-items:center;justify-content:center;letter-spacing:.5px}

/* footer */
.footer{top:4471px;left:0;width:1200px;height:459px;background:linear-gradient(180deg,#241b15,#140f0d)}
.contact{position:absolute;top:4514px;width:340px;text-align:center;color:var(--white)}
.contact .ico{width:66px;height:66px;margin:0 auto;border:2px solid rgba(255,255,255,.7);border-radius:50%;display:flex;align-items:center;justify-content:center}
.contact h3{margin-top:26px;font-size:17px;font-weight:600;letter-spacing:.5px}
.contact p{margin-top:6px;font-size:11px;line-height:22px;color:#c9c9c9}
.footer-rule{top:4695px;left:111px;width:978px;height:1px;background:rgba(255,255,255,.18)}
.footer-nav{top:4812px;left:0;width:1200px;display:flex;justify-content:center;gap:30px;font-size:11.5px;color:var(--white);font-family:"Quicksand",sans-serif;font-weight:600}
.copyright{top:4862px;left:0;width:1200px;text-align:center;color:var(--white);font-size:12px}
</style>
</head>
<body>

<header class="abs header">
  <div class="brand" style="left:111px;top:30px">
    <div class="brand-mark"></div>
    <div><div class="brand-name">1. PRAMENOVA SRO</div><div class="brand-tag">Beratungsfirma</div></div>
  </div>
  <div class="lang">English</div>
</header>

<nav class="abs nav">
  <a class="active">HOME</a><a>THE ENTERPRISE</a><a>LEISTUNGSEN</a><a>OUR PROJECTS</a><a>PARTNERS</a><a>CALL FOR COOPERATION</a><a>CONTACT</a>
</nav>

<section class="abs hero" role="img" aria-label="Craftsman in safety glasses working wood in a workshop">
  <span class="arrow" style="left:66px"><svg width="32" height="32" viewBox="0 0 32 32"><path d="M18 10l-6 6 6 6" fill="none" stroke="#fff" stroke-width="2"/></svg></span>
  <span class="arrow" style="left:1096px"><svg width="32" height="32" viewBox="0 0 32 32"><path d="M14 10l6 6-6 6" fill="none" stroke="#fff" stroke-width="2"/></svg></span>
  <h1>PRAMENOVA</h1>
  <p>Sed ut perspiciatis unde omnis iste natus error sit voluptatem accusantium doloremque laudantium, totam rem aperiam</p>
</section>
<a class="btn" style="left:494px;top:658px;width:210px;height:58px;font-size:20px">Learn More</a>

<h2 class="section-title" style="top:910px">WELCOME TO <span class="accent">PRAMENOVA</span></h2>
<p class="welcome-text">Sed ut perspiciatis unde omnis iste natus error sit voluptatem accusantium doloremque laudantium, totam rem aperiam, eaque ipsa quae ab illo inventore veritatis et quasi architecto beatae vitae dicta sunt explicabo. Nemo enim ipsam voluptatem quia voluptas sit aspernatur aut odit aut fugit, sed quia consequ untur magni dolores eos qui ratione voluptatem sequi nesciunt. Neque porro quisquam est, qui dolorem te mpora incidunt ut labore et dolore magnam aliquam quaerat voluptatem.</p>
<a class="btn" style="left:503px;top:1139px;width:192px;height:53px;font-size:18px">Read More</a>

<section class="expertise">
  <div class="abs expertise-band"></div>
  <div class="photo" style="left:111px;top:1246px;width:559px;height:415px;background:linear-gradient(135deg,#4a5a78,#2c2a33 60%,#8a7a68)" role="img" aria-label="Team of consultants working over documents at a table"></div>
  <h2>AREA OF EXPERTISE</h2>
  <p>Sed ut perspiciatis unde omnis iste natus error sit voluptatem accusantium doloremque laudantium, totam rem aperiam, eaque ipsa quae ab illo inventore veritatis et quasi architecto beatae vitae dicta sunt explicabo. Nemo enim ipsam voluptatem quia voluptas sit aspernatur aut odit aut fugit, sed quia consequuntur eos qui ratione voluptatem sequi nesciunt.</p>
  <a class="btn btn-outline" style="left:706px;top:1608px;width:163px;height:55px;font-size:18px">Read More</a>
</section>

<section>
  <h2 class="section-title" style="top:1802px">OUR <span class="accent">SERVICES</span></h2>
  <p class="section-sub" style="top:1854px">Sed ut perspiciatis unde omnis iste natus error sit voluptatem accusantium doloremque laudantium</p>
  <div class="service" style="left:134px">
    <svg width="80" height="80" viewBox="0 0 80 80" fill="none" stroke="#8cc63f" stroke-width="2.5"><path d="M12 14h22l5 6h29v50H12z"/><rect x="22" y="28" width="40" height="34"/><path d="M30 38h24M30 46h24M30 54h16"/></svg>
    <h3>PROJECT FINANCING</h3>
    <p>Sed ut perspiciatis unde omnis iste natus error sit voluptatem accusantium dolorem laudantium eaque ipsa</p>
  </div>
  <div class="service" style="left:459px">
    <svg width="80" height="80" viewBox="0 0 80 80" fill="none" stroke="#8cc63f" stroke-width="2.5"><circle cx="36" cy="42" r="26"/><ellipse cx="36" cy="42" rx="11" ry="26"/><path d="M10 42h52M14 29h44M14 55h44"/><path d="M28 52l42-36M58 14h12v12" stroke-width="3.5"/></svg>
    <h3>INTERNATIONAL DEVELOPMENT</h3>
    <p>Sed ut perspiciatis unde omnis iste natus error sit voluptatem accusantium dolorem laudantium eaque ipsa</p>
  </div>
  <div class="service" style="left:802px">
    <svg width="80" height="80" viewBox="0 0 80 80" fill="none" stroke="#8cc63f" stroke-width="2.5"><path d="M16 44l30-26 12 30-34 6z"/><path d="M24 54l8 16 7-3-5-14"/><path d="M56 22l8-8M62 32l10-2M50 14l2-9"/></svg>
    <h3>EXPORT PROMOTION</h3>
    <p>Sed ut perspiciatis unde omnis iste natus error sit voluptatem accusantium dolorem laudantium eaque ipsa</p>
  </div>
</section>

<section>
  <div class="abs partners"></div>
  <h2 class="section-title" style="top:2231px;color:var(--orange)">OUR PARTNERS</h2>
  <p class="section-sub" style="top:2283px;color:var(--white)">Sed ut perspiciatis unde omnis iste natus error sit voluptatem accusantium doloremque laudantium</p>
  <div class="partner" style="left:222px"></div>
  <div class="partner" style="left:513px"></div>
  <div class="partner" style="left:802px"></div>
</section>

<section>
  <div class="photo" style="left:111px;top:2647px;width:498px;height:414px;background:linear-gradient(180deg,#9aa0a0,#6b6f6c 55%,#4e514d)" role="img" aria-label="Warehouse hall with stacked timber pallets"></div>
  <div class="abs conditions-box">
    <h2>CONDITIONS OF <span class="accent">OUR SERVICES</span></h2>
    <p>Sed ut perspiciatis unde omnis iste natus error sit voluptatem accusantium doloremque laudantium, totam rem aperiam, eaque ipsa quae ab illo inventore veritatis et quasi architecto beatae vitae dicta sunt explicabo. Nemo enim ipsam voluptatem quia voluptas sit aspernatur aut odit aut fugit, sed quia consequuntur magni dolores eos qui ratione voluptatem quia dolor sit amet, consectetur, adipisci velit</p>
  </div>
  <a class="btn" style="left:568px;top:3076px;width:142px;height:50px;font-size:16px">Read More</a>
</section>

<section>
  <div class="abs projects-band"></div>
  <h2 class="section-title" style="top:3255px;color:var(--white)">SUCCESSFUL PROJECTS</h2>
  <p class="section-sub" style="top:3309px;color:var(--white)">Sed ut perspiciatis unde omnis iste natus error sit voluptatem accusantium doloremque laudantium</p>
  <div class="photo" style="left:111px;top:3367px;width:978px;height:543px;background:linear-gradient(180deg,#4a4a45,#8a8c88 40%,#5c5e5a 75%,#3a3b38)" role="img" aria-label="Video still of a light sport aircraft parked on a snowy apron"></div>
  <div class="play"><svg width="86" height="86" viewBox="0 0 86 86"><path d="M35 26l24 17-24 17z" fill="#fff"/></svg></div>
</section>

<section>
  <div class="abs team-band"></div>
  <h2 class="team-title">OUR TEAM</h2>
  <p class="team-text">Sed ut perspiciatis unde omnis iste natus error sit voluptatem accusantium doloremque laudantium, totam rem aperiam, eaque ipsa quae ab illo inventore veritatis et quasi architecto beatae vitae dicta sunt explicabo. Nemo enim ipsam voluptatem quia voluptas sit aspernatur aut odit aut fugit, sed quia conse quuntur magni dolores eos qui ratione voluptatem sequi nes ciunt. Neque porro quisquam est, qui dolorem ipsum quia dolor adipisci velit, sed quia non numquam</p>
  <a class="btn" style="left:111px;top:4349px;width:147px;height:53px;font-size:17px">Read More</a>
  <div class="member" style="left:536px"><div class="portrait" role="img" aria-label="Portrait photo of team member Marek Dvořan"></div><div class="name">MAREK DVOŘAN</div></div>
  <div class="member" style="left:827px"><div class="portrait" style="background:linear-gradient(180deg,#e8e6e2,#b8927a)" role="img" aria-label="Portrait photo of team member Lenka Sobotová"></div><div class="name">LENKA SOBOTOVÁ</div></div>
</section>

<footer>
  <div class="abs footer"></div>
  <div class="contact" style="left:98px">
    <div class="ico"><svg width="20" height="20" viewBox="0 0 20 20"><path d="M10 1a6 6 0 0 0-6 6c0 5 6 12 6 12s6-7 6-12a6 6 0 0 0-6-6zm0 8.5a2.5 2.5 0 1 1 0-5 2.5 2.5 0 0 1 0 5z" fill="#fff"/></svg></div>
    <h3>LOCATION</h3>
    <p>P.O. Box 201927, Lorem Ipsum DUmmy<br>Lorem Ipsum</p>
  </div>
  <div class="contact" style="left:431px">
    <div class="ico"><svg width="20" height="20" viewBox="0 0 20 20"><path d="M5 2l3 4-2 2c1 2 3 4 5 5l2-2 4 3-2 3C9 17 3 11 2 5z" fill="#fff"/></svg></div>
    <h3>CONTACT</h3>
    <p>Phone : +420 700 000 111<br>Fax: (000)-125-123</p>
  </div>
  <div class="contact" style="left:762px">
    <div class="ico"><svg width="20" height="20" viewBox="0 0 20 20"><rect x="2" y="4" width="16" height="12" rx="1" fill="#fff"/><path d="M2 5l8 6 8-6" fill="none" stroke="#241b15" stroke-width="1.5"/></svg></div>
    <h3>EMAIL</h3>
    <p>lenka@pramenova-example.eu</p>
  </div>
  <div class="abs footer-rule"></div>
  <div class="brand" style="left:466px;top:4736px">
    <div class="brand-mark"></div>
    <div><div class="brand-name" style="color:var(--white)">1. PRAMENOVA SRO</div><div class="brand-tag" style="color:var(--white)">Beratungsfirma</div></div>
  </div>
  <div class="abs footer-nav"><span>HOME</span><span>/</span><span>THE ENTERPRISE</span><span>LEISTUNGSEN</span><span>OUR PROJECTS</span><span>PARTNERS</span><span>CALL FOR COOPERATION</span><span>CONTACT</span></div>
  <p class="abs copyright">© Copyright 2019 Pramenova.All rights reserved.</p>
</footer>

</body>
</html>
```